MS Word Template for Proposals and RFP

Looking for a nice looking graphic template in MS Word. We will use this to make proposals and answer RFPs. Looking for something that will match our company brand, but give a fresh, up-to-date look and feel. There are a few pictures of a template I like. I don't necessarily like that logo - looks too "kid like" for business, but I really like how clean and organized it is. Most proposals and RFP responses are looooooonnnngggg and boring - need something that someone can look through and find what they are looking for quickly and easily.
Updates

Can't wait to see your designs!

Target Market(s)

School districts and other governmental employers

Industry/Entity Type

Business

Requirements
Must have
• Must include sample table of contents, section dividers, charts, graphs and tables that we customized based on the content. The goal is for it to look simple, clean, compelling - organized so it's easy to read, easy to find your way around - good headers, charts, flow charts, tables.... etc. Looking to have 5-10 template pages that we can use to put together and entire portfolio.
Should not have
• No "cutsie" comic sans/apple for the teacher kind of stuff - we are selling employee benefits to schools and other governmental entities. Should be more serious and conservative but also look compelling and draw in the reader.

```html
<!DOCTYPE html>
<html lang="en">
<head>
<meta charset="utf-8">
<title>Contents – Table Data</title>
<link href="https://fonts.googleapis.com/css2?family=Roboto+Condensed:wght@300;400&family=Roboto+Slab:wght@300;400&display=swap" rel="stylesheet">
<style>
  :root {
    --brand-blue: #6585c6;
    --heading-blue: #5b7fc4;
    --tab-grey: #c9c9c9;
    --body-text: #3a3a3a;
    --paper: #ffffff;
    --photo-deep: #123a78;
    --photo-light: #5d9fe0;
  }
  * { box-sizing: border-box; margin: 0; padding: 0; }
  html, body { width: 900px; height: 1200px; overflow: hidden; background: var(--paper); }
  .page { position: relative; width: 900px; height: 1200px; background: var(--paper); font-family: "Roboto Slab", "Rockwell", serif; font-weight: 300; color: var(--body-text); }

  .page-header { position: absolute; top: 0; left: 0; width: 900px; height: 63px; }
  .page-header svg { position: absolute; inset: 0; }
  .page-header__title { position: absolute; right: 16px; top: 6px; font-family: "Roboto Condensed", Arial, sans-serif; font-weight: 300; font-size: 43px; line-height: 50px; color: var(--paper); }

  .section-title { position: absolute; left: 33px; top: 104px; font-family: "Roboto Condensed", Arial, sans-serif; font-weight: 400; font-size: 27px; color: var(--heading-blue); }
  .intro { position: absolute; left: 33px; top: 139px; width: 834px; font-size: 17.5px; line-height: 34px; text-align: justify; hyphens: auto; }

  .feature { position: absolute; left: 33px; width: 828px; display: flex; justify-content: space-between; }
  .feature--one { top: 284px; }
  .feature--two { top: 600px; }
  .feature__text { width: 446px; font-size: 17.5px; line-height: 32.5px; text-align: justify; }
  .feature__photo { width: 355px; height: 258px; margin-top: 7px; background: radial-gradient(circle at 30% 20%, #cfe6ff 0%, var(--photo-light) 22%, var(--photo-deep) 75%); }

  .page-footer { position: absolute; left: 0; bottom: 0; width: 900px; height: 48px; }
  .page-footer__band { position: absolute; left: 333px; top: 0; right: 0; bottom: 0; background: var(--brand-blue); }
  .page-footer__brand { position: absolute; left: 21px; top: 10px; font-family: "Roboto Condensed", Arial, sans-serif; font-weight: 400; font-size: 22px; color: var(--brand-blue); letter-spacing: 0.5px; text-transform: uppercase; }
  .page-footer__url { position: absolute; right: 12px; top: 12px; font-size: 19px; color: var(--paper); }
</style>
</head>
<body>
<div class="page">
  <header class="page-header">
    <svg width="900" height="63" viewBox="0 0 900 63">
      <polygon points="0,0 138,0 98,63 0,63" fill="var(--tab-grey)"/>
      <polygon points="138,0 900,0 900,63 98,63" fill="var(--brand-blue)"/>
    </svg>
    <h1 class="page-header__title">Contents</h1>
  </header>

  <h2 class="section-title">Table Data</h2>
  <p class="intro">This template uses a few tables to create the page structure that follows. A host table consisting of just two columns and one row enables the sidebar content to sit beside the text, tables, and diagram on the left without any complicated positioning required.</p>

  <section class="feature feature--one">
    <p class="feature__text">Nested tables (a nested table is just one table inside another) in both the left and right column enable you to place text beside the DiagramKit graphic, provide the small financial table below left, and provide the sidebar table with a separate cell for the heading text. Nested tables (a nested table is just one table inside another) in both the left and right column enable you to place.</p>
    <div class="feature__photo" role="img" aria-label="Photo of a businesswoman touching a glowing digital interface on a blue background"></div>
  </section>

  <section class="feature feature--two">
    <p class="feature__text">Nested tables (a nested table is just one table inside another) in both the left and right column enable you to place text beside the DiagramKit graphic, provide the small financial table below left, and provide the sidebar table with a separate cell for the heading text. Nested tables (a nested table is just one table inside another) in both the left and right column enable you to place.</p>
    <div class="feature__photo" role="img" aria-label="Photo of a businesswoman touching a glowing digital interface on a blue background"></div>
  </section>

  <footer class="page-footer">
    <span class="page-footer__brand">Meridian Benefits Group</span>
    <div class="page-footer__band"></div>
    <span class="page-footer__url">www.meridianbenefits.com</span>
  </footer>
</div>
</body>
</html>
```